Harborline Auto LLC

Car Dealer Customer Service
Address: 2874 Cresthaven Road, Shelbyville, TN 37162
web: www.harborlineautoxq.net
email: harborlineautoxq@mailnest.example
Phone: (931) 555-0148
Phone: (629) 555-0173

```html
<!DOCTYPE html>
<html lang="en">
<head>
<meta charset="utf-8">
<title>Harborline Auto – Business Card</title>
<link href="https://fonts.googleapis.com/css2?family=Montserrat:wght@400;500;700&display=swap" rel="stylesheet">
<style>
  :root {
    --page-bg: #e6e6e6;
    --card-white: #ffffff;
    --brand-blue: #1e7db0;
    --accent-blue: #2b93d1;
    --ink: #1a1a1a;
  }
  * { box-sizing: border-box; margin: 0; padding: 0; }
  html, body {
    width: 1160px; height: 1200px; overflow: hidden;
    background: var(--page-bg);
    font-family: "Montserrat", Arial, sans-serif;
  }
  .canvas { position: relative; width: 1160px; height: 1200px; }
  .card {
    position: absolute; left: 199px; width: 777px; height: 442px;
  }
  .card--front { top: 104px; background: var(--card-white); }
  .card--back { top: 634px; background: var(--brand-blue); }

  .brand-mark { position: absolute; border-radius: 50%; }
  .card--front .brand-mark {
    left: 111px; top: 44px; width: 120px; height: 120px;
    background: var(--accent-blue);
  }
  .brand-name {
    position: absolute; font-weight: 700; text-transform: uppercase;
    white-space: nowrap; letter-spacing: 0.5px;
  }
  .card--front .brand-name {
    left: 35px; top: 172px; font-size: 27px; color: var(--brand-blue);
  }

  .contact-list { position: absolute; left: 27px; top: 262px; list-style: none; }
  .contact-item {
    display: flex; align-items: center; height: 31px;
    font-size: 19px; color: var(--ink); white-space: nowrap;
  }
  .contact-icon { width: 18px; height: 18px; margin-right: 12px; flex: none; }

  .address-block {
    position: absolute; right: 35px; top: 188px; text-align: right;
    font-size: 19px; line-height: 29px; color: var(--ink); font-weight: 500;
  }
  .edge-tab {
    position: absolute; right: 0; top: 201px; width: 22px; height: 70px;
    background: var(--accent-blue);
  }

  .card--back .brand-mark {
    left: 278px; top: 85px; width: 220px; height: 220px;
    border: 18px solid var(--card-white);
  }
  .card--back .brand-name {
    left: 0; right: 0; top: 336px; text-align: center;
    font-size: 48px; color: var(--card-white);
  }
</style>
</head>
<body>
<div class="canvas">
  <section class="card card--front">
    <div class="brand-mark" aria-hidden="true"></div>
    <div class="brand-name">Harborline Auto</div>

    <ul class="contact-list">
      <li class="contact-item">
        <svg class="contact-icon" viewBox="0 0 24 24" aria-hidden="true"><path fill="#2b93d1" d="M6.6 10.8a15 15 0 0 0 6.6 6.6l2.2-2.2c.3-.3.7-.4 1-.2 1.1.4 2.3.6 3.6.6.6 0 1 .4 1 1V20c0 .6-.4 1-1 1C10.6 21 3 13.4 3 4c0-.6.4-1 1-1h3.5c.6 0 1 .4 1 1 0 1.3.2 2.5.6 3.6.1.3 0 .7-.2 1z"/></svg>
        (931) 555-0148
      </li>
      <li class="contact-item">
        <svg class="contact-icon" viewBox="0 0 24 24" aria-hidden="true"><path fill="#2b93d1" d="M2 9c0-2 4-4 10-4s10 2 10 4v2h-5V9H7v2H2zM6 12h12l2 8H4z"/></svg>
        (629) 555-0173
      </li>
      <li class="contact-item">
        <svg class="contact-icon" viewBox="0 0 24 24" aria-hidden="true"><path fill="#2b93d1" d="M2 5h20v14H2z"/><path fill="none" stroke="#fff" stroke-width="1.6" d="M2 5l10 8 10-8M2 19l7-7M22 19l-7-7"/></svg>
        harborlineautoxq@mailnest.example
      </li>
      <li class="contact-item">
        <svg class="contact-icon" viewBox="0 0 24 24" aria-hidden="true"><circle cx="12" cy="12" r="10" fill="#2b93d1"/><path fill="none" stroke="#fff" stroke-width="1.4" d="M2 12h20M12 2c3 3 3 17 0 20M12 2c-3 3-3 17 0 20"/></svg>
        www.harborlineautoxq.net
      </li>
    </ul>

    <address class="address-block" style="font-style:normal">
      Car Dealer Customer Service<br>
      2874 Cresthaven Road<br>
      Shelbyville, TN 37162
    </address>
    <div class="edge-tab" aria-hidden="true"></div>
  </section>

  <section class="card card--back">
    <div class="brand-mark" aria-hidden="true"></div>
    <div class="brand-name">Harborline Auto</div>
  </section>
</div>
</body>
</html>
```